Luxury Business Card Design for High-End Window Treatments

Gilded Slatworks
Custom Plantation Shutters & Architectural Shading Systems

⸻

BACK

Daniel Trevick
Owner

Custom Interior & Exterior Window Treatments

919-555-0148
gildedslatworks.com

I have included a picture that I’m hoping we can use on the back, but I’m also wondering if you can get rid of the ladder? Should we get rid of shutters , shades and blinds underneath Gilded Slatworks?

Target Market(s)

High-end residential homeowners, custom home builders, architects, interior designers, and luxury renovation clients seeking premium plantation shutters and motorized architectural shading systems.

Industry/Entity Type

Custom Window treatments

Contact Information for Business Card

Front Gilded Slatworks Custom Plantation Shutters Motorized Architectural Shading Systems BACK Daniel Trevick Owner 919-555-0148 GildedSlatworks.com Custom Interior & Exterior Window Treatments By Appointment

Requirements
Nice to have
• Not 100% sure on nice to halves or the color but you can definitely check out my website to get a better understanding of what I’m trying to do

```html
<!DOCTYPE html>
<html lang="en">
<head>
<meta charset="utf-8">
<title>Gilded Slatworks – Business Card</title>
<link rel="stylesheet" href="https://fonts.googleapis.com/css2?family=Gilda+Display&family=Playfair+Display:wght@600&display=swap">
<style>
  :root {
    --page-bg: #5c5b5c;
    --card-dark: #1f201d;
    --gold: #f2cd5c;
    --cream: #efe9dc;
    --frame-gold: #c9a545;
    --panel-dark: rgba(24, 24, 22, 0.55);
    --sky: #8fb6d8;
    --siding: #c9c4b4;
    --foliage: #4b5a3a;
    --lawn: #6c7044;
  }
  * { margin: 0; padding: 0; box-sizing: border-box; }
  html, body { width: 1200px; height: 800px; overflow: hidden; }
  body {
    background: var(--page-bg);
    font-family: "Gilda Display", Georgia, serif;
    display: flex;
    align-items: center;
    justify-content: center;
    gap: 40px;
  }
  .card {
    position: relative;
    width: 530px;
    height: 303px;
    border-radius: 18px;
    overflow: hidden;
    box-shadow: 0 10px 28px rgba(0, 0, 0, 0.3);
  }

  /* Front */
  .card--front { background: var(--card-dark); }
  .brand {
    position: absolute;
    left: 0; right: 0; top: 88px;
    text-align: center;
  }
  .brand__name {
    font-family: "Gilda Display", Georgia, serif;
    color: var(--cream);
    font-size: 40px;
    line-height: 1;
    letter-spacing: 0.5px;
  }
  .brand__lines {
    margin-top: 14px;
    font-family: "Playfair Display", Georgia, serif;
    font-weight: 600;
    color: var(--gold);
    font-size: 15px;
    word-spacing: 10px;
    letter-spacing: 0.5px;
  }
  .front__tagline {
    position: absolute;
    left: 0; right: 0; bottom: 34px;
    text-align: center;
    color: var(--gold);
    font-size: 12.5px;
    letter-spacing: 0.6px;
  }

  /* Back */
  .card--back {
    background:
      linear-gradient(180deg, var(--sky) 0%, #a9c3d8 18%, var(--siding) 30%, #3e4450 45%, #3a3d40 62%, var(--foliage) 76%, var(--lawn) 100%);
  }
  .back__photo { position: absolute; inset: 0; }
  .contact-panel {
    position: absolute;
    left: 50px; right: 50px; top: 48px; bottom: 48px;
    border: 1.5px solid var(--frame-gold);
    background: var(--panel-dark);
    color: var(--gold);
    text-align: center;
    padding-top: 18px;
  }
  .person__name { font-size: 27px; line-height: 1.05; }
  .person__role { font-size: 19px; line-height: 1.1; }
  .person__rule {
    width: 110px; height: 1.5px;
    margin: 7px auto 12px;
    background: var(--gold);
  }
  .contact-line {
    display: flex;
    align-items: center;
    justify-content: center;
    gap: 7px;
    font-size: 15px;
    letter-spacing: 0.8px;
    line-height: 1.5;
  }
  .contact-line svg { width: 12px; height: 12px; flex: none; }
  .service-note {
    margin-top: 14px;
    font-size: 13.5px;
    letter-spacing: 0.8px;
  }
</style>
</head>
<body>

  <section class="card card--front" aria-label="Business card front">
    <div class="brand">
      <div class="brand__name">Gilded Slatworks</div>
      <div class="brand__lines">Shutters Shades Blinds</div>
    </div>
    <p class="front__tagline">Custom Plantation Shutters &amp; Motorized Architectural Shading Systems</p>
  </section>

  <section class="card card--back" aria-label="Business card back">
    <div class="back__photo" role="img" aria-label="Photograph of a home's screened back porch with motorized exterior shades, stone columns, garden and Adirondack chairs"></div>
    <div class="contact-panel">
      <div class="person__name">Daniel Trevick</div>
      <div class="person__role">Owner</div>
      <div class="person__rule"></div>

      <div class="contact-line">
        <svg viewBox="0 0 24 24" fill="none" stroke="currentColor" stroke-width="2" stroke-linecap="round" stroke-linejoin="round" aria-hidden="true">
          <path d="M22 16.9v3a2 2 0 0 1-2.2 2 19.8 19.8 0 0 1-8.6-3.1 19.5 19.5 0 0 1-6-6A19.8 19.8 0 0 1 2.1 4.2 2 2 0 0 1 4.1 2h3a2 2 0 0 1 2 1.7c.1.9.4 1.8.7 2.7a2 2 0 0 1-.5 2.1L8 9.8a16 16 0 0 0 6 6l1.3-1.3a2 2 0 0 1 2.1-.4c.9.3 1.8.6 2.7.7a2 2 0 0 1 1.7 2z"/>
        </svg>
        <span>919-555-0148</span>
      </div>
      <div class="contact-line">
        <svg viewBox="0 0 24 24" fill="none" stroke="currentColor" stroke-width="2" aria-hidden="true">
          <circle cx="12" cy="12" r="10"/>
          <path d="M2 12h20M12 2a15 15 0 0 1 0 20M12 2a15 15 0 0 0 0 20"/>
        </svg>
        <span>gildedslatworks.com</span>
      </div>
      <div class="contact-line">
        <svg viewBox="0 0 24 24" fill="none" stroke="currentColor" stroke-width="2" stroke-linecap="round" stroke-linejoin="round" aria-hidden="true">
          <path d="M3 8h4l5 4 5-4h4M7 8v8l4 3M17 8v8l-4 3"/>
        </svg>
        <span>Custom Interior &amp; Exterior Window Treatments</span>
      </div>

      <div class="service-note">BY APPOINTMENT</div>
    </div>
  </section>

</body>
</html>
```